Local massage therapist needs some new marketing material

Hi there! I am a massage therapist here in Denver, CO in Alder Bend(shopping and art district) of the city. My business is called Lumo Bodywork of Denver. My practice has an eastern influence and I do reflexology, thai massage and use Chinese herbs, etc. I know all my clients and pay close attention to details. I am also very respectful of tradition and it shows in how I work. I tend to like modern, clean, fun, Asian designs. I am wanting a new business card and brochure. I have a logo and branding for my business that I want used in the design. Currently, the sign for my building is purple and I think my logo was designed to be purple. I will attach pictures of it and can send whatever files are necessary so it can be integrated into the brochure, etc. I like the purple but open to using other colors as well. Thanks!
My website is lumobodyworkofdenver.example where info can be gathered about me and services/fees for brochure.
Updates

Just increased budget. Please see new feedback in discussion thread.

Thanks!

                                       HEY ALL,

Just wanted to let you know that I made a change to my website. It is on the Prices Page. I no longer have the frequent  flyer prices but I added discounts. Let me know if you have any questions. Thanks so much!

Target Market(s)

healthy, urban, educated, upper middle class, yogis

Industry/Entity Type

Marketing

Requirements
Must have
• logo stays purple
Should not have
• not too busy

```html
<!DOCTYPE html>
<html lang="en">
<head>
<meta charset="utf-8">
<title>Lumo Bodywork of Denver — Stationery</title>
<link rel="stylesheet" href="https://fonts.googleapis.com/css2?family=Roboto+Slab:wght@300&family=Open+Sans:wght@300;400&display=swap">
<style>
  :root{
    --page-bg:#ece8ef;
    --paper:#ffffff;
    --purple-deep:#6d3d97;
    --purple-bright:#9a5ccb;
    --purple-card:#7b4ea1;
    --purple-ink:#5a2d8c;
    --white:#ffffff;
  }
  *{box-sizing:border-box;margin:0;padding:0}
  html,body{width:1200px;height:1200px;overflow:hidden}
  body{background:var(--page-bg);position:relative;font-family:"Open Sans",sans-serif}

  /* Letterhead */
  .letterhead{position:absolute;left:27px;top:253px;width:580px;height:818px;background:var(--paper);box-shadow:0 2px 8px rgba(0,0,0,.15);overflow:hidden}
  .letterhead__brand{position:absolute;left:14px;top:16px;width:80px;text-align:center;color:var(--purple-ink)}
  .brand-mark{display:block;margin:0 auto;border:2px solid currentColor;border-radius:50%}
  .letterhead__brand .brand-mark{width:54px;height:54px}
  .brand-name{font-family:"Open Sans",sans-serif;font-weight:300;letter-spacing:.18em}
  .letterhead__brand .brand-name{font-size:17px;margin-top:12px;padding-left:.18em}
  .letterhead__body{position:absolute;left:14px;top:150px;width:540px;font-family:"Roboto Slab",serif;font-weight:300;font-size:18.5px;line-height:22.5px;color:var(--purple-ink)}
  .letterhead__body p{margin-bottom:4px}
  .letterhead__swoosh{position:absolute;left:0;bottom:0;width:580px;height:300px}

  /* Business card front */
  .card-front{position:absolute;left:612px;top:289px;width:547px;height:311px;background:var(--paper);box-shadow:0 2px 8px rgba(0,0,0,.15);overflow:hidden}
  .card-front__panel{position:absolute;inset:0;width:547px;height:311px}
  .card-front__person{position:absolute;left:17px;top:8px;color:var(--white);font-size:24px;line-height:24px;font-weight:400}
  .card-front__person span{display:block;padding-left:3px}
  .contact-list{position:absolute;left:28px;top:174px;list-style:none;color:var(--white);font-size:11.5px;line-height:15.5px}
  .contact-list li{display:flex;align-items:center;gap:5px}
  .contact-list svg{width:8px;height:8px;flex:none}
  .card-front__brand{position:absolute;left:378px;top:120px;width:140px;text-align:center;color:var(--purple-ink)}
  .card-front__brand .brand-mark{width:86px;height:86px}
  .card-front__brand .brand-name{font-size:26px;margin-top:40px;padding-left:.18em}

  /* Business card back */
  .card-back{position:absolute;left:615px;top:636px;width:553px;height:347px;background:var(--purple-card);border:6px solid var(--white);box-shadow:0 2px 8px rgba(0,0,0,.15);text-align:center;color:var(--white)}
  .card-back .brand-mark{width:176px;height:176px;margin-top:52px;border-width:2.5px}
  .card-back .brand-name{font-size:28px;margin-top:42px;padding-left:.18em;font-weight:400}
</style>
</head>
<body>

<section class="letterhead" aria-label="Letterhead">
  <div class="letterhead__brand">
    <span class="brand-mark" aria-hidden="true"></span>
    <div class="brand-name">LUMO</div>
  </div>
  <div class="letterhead__body">
    <p>Started several mistake joy say painful removed reached end. State burst think end are its. Arrived off she elderly beloved him affixed noisier yet. An course regard to up he hardly. View four has said does men saw find dear shy. Talent men wicket add garden.</p>
    <p>Started several mistake joy say painful removed reached end. State burst think end are its. Arrived off she elderly beloved him affixed noisier yet. An course regard to up he hardly. View four has said does men saw find dear shy. Talent men wicket add garden.</p>
    <p>Started several mistake joy say painful removed reached end. State burst think end are its. Arrived off she elderly beloved him affixed noisier yet. An course regard to up he hardly. View four has said does men saw find dear shy. Talent men wicket add garden.</p>
    <p>Started several mistake joy say painful removed reached end. State burst think end are its. Arrived off she elderly beloved him affixed noisier yet. An course regard to up he hardly. View four has said does men saw find dear shy. Talent men wicket add garden.</p>
  </div>
  <svg class="letterhead__swoosh" viewBox="0 0 580 300" preserveAspectRatio="none" aria-hidden="true">
    <path d="M0 300 C200 250 430 170 580 20 L580 90 C440 190 220 262 0 300 Z" fill="var(--purple-bright)"/>
    <path d="M0 300 C220 262 440 190 580 90 L580 300 Z" fill="var(--purple-deep)"/>
  </svg>
</section>

<section class="card-front" aria-label="Business card, front">
  <svg class="card-front__panel" viewBox="0 0 547 311" preserveAspectRatio="none" aria-hidden="true">
    <path d="M348 0 L445 0 C380 60 320 170 272 311 L262 311 C290 180 320 80 348 0 Z" fill="var(--purple-bright)"/>
    <path d="M0 0 L335 0 C305 90 285 200 272 311 L0 311 Z" fill="var(--purple-deep)"/>
  </svg>
  <div class="card-front__person">
    <span>Your Name</span>
    <span>Designation</span>
  </div>
  <ul class="contact-list">
    <li><svg viewBox="0 0 8 8"><path d="M4 0 L8 4 L7 4 L7 8 L1 8 L1 4 L0 4 Z" fill="currentColor"/></svg>1475 E Linden Ave, Denver, CO 80206</li>
    <li><svg viewBox="0 0 8 8"><circle cx="4" cy="4" r="3.5" fill="currentColor"/></svg>303.555.0142</li>
    <li><svg viewBox="0 0 8 8"><rect x=".5" y="1.5" width="7" height="5" fill="none" stroke="currentColor"/></svg>info@lumobodyworkdenver.example</li>
    <li><svg viewBox="0 0 8 8"><path d="M2 0 L4 2 L3 3 C3.5 4.5 4 5 5 5 L6 4 L8 6 L6 8 C3 8 0 5 0 2 Z" fill="currentColor"/></svg>303.555.0142</li>
    <li><svg viewBox="0 0 8 8"><circle cx="4" cy="4" r="3.5" fill="none" stroke="currentColor"/></svg>www.lumobodyworkofdenver.example</li>
  </ul>
  <div class="card-front__brand">
    <span class="brand-mark" aria-hidden="true"></span>
    <div class="brand-name">LUMO</div>
  </div>
</section>

<section class="card-back" aria-label="Business card, back">
  <span class="brand-mark" aria-hidden="true"></span>
  <div class="brand-name">LUMO</div>
</section>

</body>
</html>
```